Veltrane Group Business Card Design

The CEO is looking for a new trendy look for his business card.
You can stay with current branding or come up with something new/creative. It can be 3D, including Medical Office buildings. You can use our logo in a variety of colors. Please include name, title, company name, company website, email address, cell number

Target Market(s)

Real Estate Development and Construction

Industry/Entity Type

Health care real estate

Contact Information for Business Card

Rohesh Kamdar, CEO M-604.781.2249 E-roheshkamdar@veltrane.com Address:4180 Lindqvist Ave, Tampa, FL 33482 www.veltrane.com

Font styles to use
Other font styles liked:
• Be creative

Requirements
Must have
• Creative, trendy look
Nice to have
• Please go to our website to get a feel- www. veltrane.com
Should not have
• small fonts

```html
<!DOCTYPE html>
<html lang="en">
<head>
<meta charset="utf-8">
<title>Veltrane Group – Business Card</title>
<link rel="stylesheet" href="https://fonts.googleapis.com/css2?family=Montserrat:wght@400;500;700;800&display=swap">
<style>
  :root {
    --brand-red: #b01f2a;
    --brand-navy: #1b2b4e;
    --card-white: #ffffff;
    --ink: #1d1d1f;
    --backdrop: #2a2a2c;
  }
  * { margin: 0; padding: 0; box-sizing: border-box; }
  html, body { width: 1200px; height: 874px; overflow: hidden; }
  body {
    background: var(--backdrop);
    font-family: "Montserrat", sans-serif;
    display: flex;
    flex-direction: column;
    align-items: center;
    justify-content: center;
    gap: 40px;
  }
  .card {
    position: relative;
    width: 660px;
    height: 377px;
    background: var(--card-white);
    border-radius: 22px;
    overflow: hidden;
  }
  .card-band {
    position: absolute;
    left: 0; bottom: 0;
    width: 100%; height: 34px;
  }
  .front .brand-name {
    position: absolute;
    left: 0; right: 0; top: 130px;
    text-align: center;
    font-weight: 800;
    font-size: 74px;
    letter-spacing: -2px;
    color: var(--brand-red);
  }
  .back .brand-name {
    position: absolute;
    left: 30px; top: 150px;
    width: 300px;
    text-align: right;
    font-weight: 800;
    font-size: 36px;
    letter-spacing: -1px;
    color: var(--brand-red);
    line-height: 1.1;
  }
  .divider {
    position: absolute;
    left: 350px; top: 100px;
    width: 2px; height: 160px;
    background: var(--brand-red);
  }
  .contact {
    position: absolute;
    left: 370px; top: 102px;
    color: var(--ink);
  }
  .contact .person {
    font-weight: 700;
    font-size: 24px;
    color: var(--brand-red);
  }
  .contact .role {
    font-size: 15px;
    margin-bottom: 12px;
  }
  .contact ul { list-style: none; }
  .contact li {
    display: flex;
    align-items: center;
    gap: 8px;
    font-size: 15px;
    margin-bottom: 6px;
  }
  .contact li svg { width: 13px; height: 13px; fill: var(--brand-red); flex: none; }
  .contact .address { font-size: 15px; line-height: 1.25; margin-top: 6px; }
</style>
</head>
<body>
  <section class="card front">
    <div class="brand-name">Veltrane Group</div>
    <svg class="card-band" viewBox="0 0 660 34" preserveAspectRatio="none">
      <polygon points="0,0 300,34 0,34" fill="var(--brand-navy)"/>
      <polygon points="310,0 660,0 660,34 300,34 318,12" fill="var(--brand-red)"/>
      <polygon points="0,0 310,0 300,34" fill="var(--card-white)"/>
    </svg>
  </section>

  <section class="card back">
    <div class="brand-name">Veltrane<br>Group</div>
    <div class="divider"></div>
    <div class="contact">
      <div class="person">Rohesh Kamdar</div>
      <div class="role">CEO</div>
      <ul>
        <li><svg viewBox="0 0 16 16"><path d="M3.6 1.2l2.6 2.6-1.4 2a9 9 0 0 0 5.4 5.4l2-1.4 2.6 2.6-1.8 2.2C7.5 16 0 8.5 1.4 3z"/></svg>604.781.2249</li>
        <li><svg viewBox="0 0 16 16"><path d="M1 3h14v10H1z M1 3l7 6 7-6" /></svg>roheshkamdar@veltrane.com</li>
        <li><svg viewBox="0 0 16 16"><circle cx="8" cy="8" r="7"/></svg>www.veltrane.com</li>
      </ul>
      <div class="address">4180 Lindqvist Ave,<br>Tampa, FL 33482</div>
    </div>
    <svg class="card-band" viewBox="0 0 660 34" preserveAspectRatio="none">
      <polygon points="0,0 300,34 0,34" fill="var(--brand-navy)"/>
      <polygon points="310,0 660,0 660,34 300,34 318,12" fill="var(--brand-red)"/>
      <polygon points="0,0 310,0 300,34" fill="var(--card-white)"/>
    </svg>
  </section>
</body>
</html>
```